Designing a brochures for an educational counseling service provider

We would like a 4 sided design on a 11x8.5 paper, half folded. I have including a sample design we did to give you an idea of what we envision but we welcome creativity to make beautiful looking flyers. Text for the flier is included as well as our logo.
- The most important thing is capturing our audience/market. We will be handing these flies to schools, organizations and individual clients.

www.pvrlearningadvisors.example

Target Market(s)

We are targeting international students wanting to study in the U.S and Canada.

Industry/Entity Type

Education

Requirements
Must have
• - Clean and clear
• - Our logo should visible and well placed.
• - Could you the pictures of students, libraries and school buildings or you could use the pictures we already have.
Nice to have
• We would like this to match business cards.

```html
<!DOCTYPE html>
<html lang="en">
<head>
<meta charset="utf-8">
<title>PVR Learning Advisors – Brochure Spread</title>
<link href="https://fonts.googleapis.com/css2?family=Montserrat:wght@500;700;800&family=Oswald:wght@400&display=swap" rel="stylesheet">
<style>
  :root {
    --backdrop: #a7a7a7;
    --orange: #f77b0c;
    --navy: #0f2a5c;
    --green: #6cb33a;
    --white: #ffffff;
    --logo-box: #15304a;
    --icon-ring: #f0a566;
    --icon-line: #7a7f88;
  }
  html, body {
    margin: 0;
    padding: 0;
    width: 948px;
    height: 1200px;
    overflow: hidden;
    background: var(--backdrop);
  }
  .spread {
    position: absolute;
    left: 24px;
    top: 252px;
    width: 900px;
    height: 695px;
    box-shadow: 0 8px 18px rgba(0,0,0,0.35);
  }
  .spread svg { display: block; width: 100%; height: 100%; }
  .heading { font-family: 'Montserrat', sans-serif; font-weight: 800; fill: var(--white); }
  .contact { font-family: 'Montserrat', sans-serif; font-weight: 500; fill: var(--white); }
  .contact-strong { font-family: 'Montserrat', sans-serif; font-weight: 700; fill: var(--white); }
  .brand-name { font-family: 'Montserrat', sans-serif; font-weight: 700; fill: var(--white); }
  .service-label { font-family: 'Montserrat', sans-serif; font-weight: 700; fill: var(--navy); }
  .tagline { font-family: 'Oswald', sans-serif; font-weight: 400; fill: var(--navy); }
  .web { font-family: 'Montserrat', sans-serif; font-weight: 700; fill: var(--white); }
  .icon-ring { fill: var(--white); stroke: var(--icon-ring); stroke-width: 2; }
  .icon-line { fill: none; stroke: var(--icon-line); stroke-width: 1.4; stroke-linejoin: round; stroke-linecap: round; }
</style>
</head>
<body>
<div class="spread">
  <svg viewBox="0 0 782 604" xmlns="http://www.w3.org/2000/svg">
    <defs>
      <clipPath id="photo-window">
        <path d="M60,545 C25,420 95,260 210,172 C420,60 700,62 782,150 L782,195 L745,212 C545,392 300,560 60,560 Z"/>
      </clipPath>
      <linearGradient id="library-tones" x1="0" y1="0" x2="1" y2="1">
        <stop offset="0" stop-color="#e9e4da"/>
        <stop offset="0.5" stop-color="#b8b2a8"/>
        <stop offset="1" stop-color="#8e93a6"/>
      </linearGradient>
      <linearGradient id="campus-tones" x1="0" y1="0" x2="1" y2="1">
        <stop offset="0" stop-color="#b98a5e"/>
        <stop offset="0.5" stop-color="#6e4630"/>
        <stop offset="1" stop-color="#3b2a22"/>
      </linearGradient>
    </defs>

    <!-- page base -->
    <rect class="page-base" x="0" y="0" width="782" height="604" fill="var(--orange)"/>
    <path class="right-page-field" d="M430,0 L782,0 L782,585 L391,585 L391,300 Z" fill="var(--white)"/>

    <!-- photo areas -->
    <g clip-path="url(#photo-window)">
      <rect role="img" aria-label="Photo: smiling student holding a red book in a library" x="0" y="0" width="391" height="604" fill="url(#library-tones)"/>
      <rect role="img" aria-label="Photo: smiling student with a backpack on campus" x="391" y="0" width="391" height="604" fill="url(#campus-tones)"/>
    </g>

    <!-- swooshes -->
    <path class="navy-swoosh" d="M0,490 C-10,625 330,612 565,400 L775,198 L745,212 C545,392 300,560 60,560 C25,560 8,530 0,490 Z" fill="var(--navy)"/>
    <path class="green-swoosh" d="M160,188 C320,50 620,0 782,55 L782,175 C720,70 430,60 210,172 Z" fill="var(--green)"/>

    <!-- bottom band -->
    <rect class="bottom-band" x="391" y="585" width="391" height="19" fill="var(--orange)"/>
    <text class="web" x="585" y="598" font-size="9" text-anchor="middle">www.pvrlearningadvisors.example</text>

    <!-- fold line -->
    <line x1="391" y1="0" x2="391" y2="604" stroke="rgba(0,0,0,0.12)" stroke-width="1"/>

    <!-- contact panel -->
    <text class="heading" x="32" y="52" font-size="22">CONTACT US</text>
    <text class="contact" x="31" y="72" font-size="8.5">Executive Director &amp; Independent</text>
    <text class="contact" x="31" y="84" font-size="8.5">Educational Consultant</text>
    <text class="contact" x="31" y="96" font-size="8.5">PVR Learning Advisors, LLC</text>

    <path d="M34,111 a3,3 0 1 1 0.01,0 M31,112 L34,118 L37,112" fill="var(--white)"/>
    <text class="contact" x="49" y="119" font-size="9.5">4180 Meadow Ridge Rd</text>
    <text class="contact" x="49" y="132" font-size="9.5">Suite 310, Fairview, TX 75069</text>

    <path d="M28,149 q5,-4 10,0 l-1,3 h-2 v-1.5 h-4 v1.5 h-2 Z M30,151 h6 v4 h-6 Z" fill="var(--white)"/>
    <text class="contact-strong" x="48" y="154" font-size="12">555-014-2276</text>

    <rect x="29" y="167" width="8" height="6" fill="none" stroke="var(--white)" stroke-width="1"/>
    <path d="M29,167 L33,171 L37,167" fill="none" stroke="var(--white)" stroke-width="1"/>
    <text class="contact" x="48" y="173" font-size="8.5">info@pvrlearningadvisors.example</text>

    <!-- brand marks -->
    <rect x="248" y="10" width="141" height="56" fill="var(--logo-box)"/>
    <text class="brand-name" x="318" y="35" font-size="11" text-anchor="middle">PVR Learning</text>
    <text class="brand-name" x="318" y="50" font-size="11" text-anchor="middle">Advisors</text>

    <rect x="643" y="192" width="139" height="56" fill="var(--logo-box)"/>
    <text class="brand-name" x="712" y="217" font-size="11" text-anchor="middle">PVR Learning</text>
    <text class="brand-name" x="712" y="232" font-size="11" text-anchor="middle">Advisors</text>

    <!-- services -->
    <g class="service">
      <circle class="icon-ring" cx="682" cy="325" r="25"/>
      <circle class="icon-line" cx="676" cy="316" r="4"/>
      <path class="icon-line" d="M668,332 v-5 q8,-6 16,0 v5 Z"/>
      <circle class="icon-line" cx="690" cy="322" r="3.5"/>
      <path class="icon-line" d="M684,333 q6,-8 13,0 Z"/>
      <text class="service-label" x="717" y="322" font-size="9">Graduate</text>
      <text class="service-label" x="717" y="334" font-size="9">Students</text>
    </g>
    <g class="service">
      <circle class="icon-ring" cx="617" cy="392" r="25"/>
      <path class="icon-line" d="M603,388 L617,381 L631,388 L617,395 Z M609,391 v8 q8,5 16,0 v-8"/>
      <text class="service-label" x="654" y="389" font-size="9">Transfer</text>
      <text class="service-label" x="654" y="401" font-size="9">Students</text>
    </g>
    <g class="service">
      <circle class="icon-ring" cx="543" cy="450" r="25"/>
      <path class="icon-line" d="M534,438 h13 l5,5 v18 h-18 Z"/>
      <path class="icon-line" d="M540,456 l10,-10 l3,3 l-10,10 h-3 Z"/>
      <text class="service-label" x="578" y="451" font-size="9">College</text>
      <text class="service-label" x="578" y="463" font-size="9">Admission</text>
    </g>
    <g class="service">
      <circle class="icon-ring" cx="462" cy="500" r="25"/>
      <path class="icon-line" d="M449,492 L462,485 L475,492 Z M450,494 h24 M453,496 v11 M458,496 v11 M462,496 v11 M466,496 v11 M471,496 v11 M449,509 h26"/>
      <text class="service-label" x="498" y="502" font-size="9">Boarding</text>
      <text class="service-label" x="498" y="514" font-size="9">Schools</text>
    </g>

    <!-- tagline -->
    <text class="tagline" x="765" y="505" font-size="15.5" text-anchor="end">A full-service international</text>
    <text class="tagline" x="765" y="528" font-size="15.5" text-anchor="end">educational consulting group</text>
    <text class="tagline" x="765" y="551" font-size="15.5" text-anchor="end">serving students and families</text>
    <text class="tagline" x="765" y="574" font-size="15.5" text-anchor="end">across the globe.</text>
  </svg>
</div>
</body>
</html>
```